A Techincal Author needs a site to promote his Programming Books

The StudyAlong series is a collection of books focusing on building the same app with different technologies. The purpose of this project is to design a web site home page that can be used to sell the books.

Expected Deliverables
• StudyAlong Logo as Illustrator file
• Master graphic design files for any relevant web assets
• HTML and CSS for home page, if applicable

Target Market(s)

The target market for our series is web programmers. They are people who have some experience, but want to learn a new tool. Programmers are analytical, logical people who like structure in the things they do.

Here are some things our customers like:

• Chirply / Postbox
• Crown of Ashes / Hollow Tide / Salt Hollow
• SmartPhones, Tablets, Stridelets, and other tech gadgets.

The design should try to speak to that market.

Requirements
Must have
• The primary tasks for this project are:
• 1) Create "Study Along" Logo.
• * All “NetPivot” properties use a similar logo approach, with the NetPivot ball icon on the left, a reflection below it. The company name is on the right, roughly the same size as the ball icon. A tag line underneath the company name, roughly the same size as the reflection.
• * Company Name: Study Along
• * Tagline: Knowledge to Boost Your Career
• * Logo color is up to the discretion of the designer, but should be compatible with the site design.
• * Sample Logos for other NetPivot properties in Illustrator format are available as attachments to this project.
• 2) Design the Study Along Home Page.
• The home page should follow this format:
• * Logo
• * Nav Bar
• • Buy (The Home Page)
• • About
• • Contact
• * Main Content
• • Home page content detailed in attachment
• * Footer
• • Copyright notice
• • Links to other stuff we do ( net-pivot.example | marlonpeake.example | BeyondTheGrid.example )
Nice to have
• It would be nice to have a book as part of the home page content.
Should not have
• Please do not use the same color scheme as BeyondTheGrid.example or Plumvane.example or QueryTheMaven.example

```html
<!DOCTYPE html>
<html lang="en">
<head>
<meta charset="utf-8">
<title>StudyAlong – Home</title>
<link rel="stylesheet" href="https://fonts.googleapis.com/css2?family=Montserrat:wght@500;600&family=Open+Sans:wght@300;400;600&family=Roboto:wght@300;400&display=swap">
<style>
:root{
  --orange:#f5b100;
  --orange-deep:#ee6a0c;
  --green:#8cc21e;
  --ink:#333;
  --muted:#9a9a9a;
  --line:#e2e2e2;
  --panel:#f3f3f3;
  --footer:#efefef;
}
*{box-sizing:border-box;margin:0;padding:0}
html,body{width:747px;height:1200px;overflow:hidden;background:#fff}
body{position:relative;font-family:"Open Sans",sans-serif;color:var(--ink)}
.abs{position:absolute}

/* header */
.site-header{position:absolute;left:0;top:0;width:747px;height:58px;background:#fff}
.brand{position:absolute;left:95px;top:14px;font-family:"Montserrat",sans-serif;font-weight:600;font-size:24px;color:var(--orange);letter-spacing:-.3px}
.main-nav{position:absolute;top:24px;left:298px;display:flex;gap:0}
.main-nav a{position:absolute;font-size:11px;color:var(--muted);text-decoration:none;white-space:nowrap}
.main-nav a.active{color:var(--ink)}
.nav-marker{position:absolute;left:296px;top:57px;width:40px;height:2px;background:var(--orange)}

/* hero */
.hero{position:absolute;left:0;top:58px;width:747px;height:304px;
  background:radial-gradient(ellipse at 35% 55%,#c77a4a 0%,#9b4f2c 40%,#5a2a1c 100%)}
.hero-title{position:absolute;left:97px;top:114px;font-family:"Montserrat",sans-serif;font-weight:600;font-size:24px;line-height:29px;color:#fff;letter-spacing:-.2px}
.hero-title span{color:var(--orange)}
.slider-dots{position:absolute;left:100px;top:184px;display:flex;gap:3px}
.slider-dots i{display:block;width:11px;height:11px;border-radius:50%;background:#fff}
.slider-dots i.current{background:transparent;border:2px solid #fff}
.signup{position:absolute;left:470px;top:52px;width:192px;height:174px;background:var(--orange);padding:4px}
.signup-inner{width:100%;height:100%;border:1px solid rgba(255,255,255,.55);position:relative}
.signup h2{font-family:"Roboto",sans-serif;font-weight:400;font-size:16px;line-height:19px;color:#fff;text-align:center;margin-top:22px}
.signup .field{position:absolute;left:18px;width:151px;height:20px;background:#fff;border:1px solid #e5e5e5;font-size:7px;color:#aaa;padding:6px 8px}
.signup .submit{position:absolute;left:18px;top:124px;width:151px;height:28px;border:2px solid #fff;color:#fff;font-family:"Roboto",sans-serif;font-size:13px;text-align:center;line-height:24px}

/* about */
.about{position:absolute;left:0;top:362px;width:747px;height:238px;background:var(--panel);border-bottom:1px solid #cfcfcf}
.about-visual{position:absolute;left:108px;top:36px;width:207px;height:202px;background:linear-gradient(160deg,#e8c3a2,#c99472)}
.about h2{position:absolute;left:339px;top:39px;font-family:"Roboto",sans-serif;font-weight:300;font-size:20px;color:#444}
.about p{position:absolute;left:339px;top:72px;width:318px;font-size:8px;line-height:17px;color:var(--muted)}
.btn-more{position:absolute;left:339px;top:181px;width:71px;height:22px;background:var(--green);color:#fff;font-size:6.5px;font-weight:600;text-align:center;line-height:22px;border-radius:2px}

/* book tables */
.book{position:absolute;left:107px;width:529px;border:1px solid #d9d9d9;background:#fff}
.book-head{height:28px;color:#fff;font-size:11px;padding:0 16px;display:flex;justify-content:space-between;align-items:center}
.book-head .view{font-size:8px;font-weight:600;display:flex;align-items:center;gap:4px}
.book.orange .book-head{background:linear-gradient(#fbbc0c,#f29d00)}
.book.rust .book-head{background:linear-gradient(#f47c12,#e35b06)}
.book.green .book-head{background:linear-gradient(#a5d72d,#87c01c)}
.book-rows{padding:4px 0 12px}
.book-row{position:relative;height:19px;margin:0 6px;font-size:8.5px;color:var(--muted);line-height:19px}
.book-row + .book-row{border-top:1px solid var(--line)}
.book-row span{position:absolute}
.c1{left:22px}.c2{left:176px}.c3{left:244px}.c4{left:347px}

/* footer */
.site-footer{position:absolute;left:0;top:1052px;width:747px;height:148px;background:var(--footer)}
.partner{position:absolute;top:30px;display:flex;align-items:center;gap:5px;font-family:"Open Sans",sans-serif;font-weight:600;font-size:16px;white-space:nowrap}
.partner i{display:block;width:14px;height:14px;border-radius:50%}
.footer-rule{position:absolute;left:107px;top:78px;width:523px;height:1px;background:#d6d6d6}
.footer-nav a{position:absolute;top:91px;font-size:10.5px;color:#555;text-decoration:none}
.copyright{position:absolute;left:109px;top:111px;font-size:7px;color:#999}
.social{position:absolute;top:86px;width:22px;height:22px;border-radius:50%;border:1px solid #aaa}
</style>
</head>
<body>

<header class="site-header">
  <div class="brand">StudyAlong</div>
  <nav class="main-nav">
    <a class="active" style="left:0">Home</a>
    <a style="left:46px">About Us</a>
    <a style="left:109px">Technology</a>
    <a style="left:182px">Shop Book</a>
    <a style="left:251px">Resources</a>
    <a style="left:318px">Contact</a>
  </nav>
  <div class="nav-marker"></div>
</header>

<section class="hero" role="img" aria-label="Photo of hands holding a tablet in warm light">
  <h1 class="hero-title">KNOWLEDGE TO BOOST<br><span>YOUR CAREER</span></h1>
  <div class="slider-dots"><i class="current"></i><i></i><i></i><i></i></div>
  <form class="signup">
    <div class="signup-inner">
      <h2>SIGN UP FOR<br>A FREE SAMPLE</h2>
      <div class="field" style="top:66px">First Name</div>
      <div class="field" style="top:93px">Email Address</div>
      <div class="submit">SUBMIT</div>
    </div>
  </form>
</section>

<section class="about">
  <div class="about-visual" role="img" aria-label="Illustration of hands holding a tablet showing the StudyAlong name and a click here button"></div>
  <h2>About Study Along</h2>
  <p>Donec quis mi sed magna hendrerit accumsan Suspendisse risus nibh ultricies eu volutpat non condimentum hendrerit augue<br>Maecenas aliquet velit vel turpis Mauris neque metus malesuada nec ultricies sit amet porttitor mattis enim In massa libero interdum nec interdum vel blandit sed nulla In ullamcorper est eget tempor cursus neque mi consectetuer mi a ultricies massa est sed nisl Class aptent taciti sociosqu</p>
  <div class="btn-more">READ MORE</div>
</section>

<section class="book orange" style="top:625px">
  <div class="book-head"><span>AnvilJS 1.5 &amp; Strapkit</span><span class="view">View App <svg width="5" height="8" viewBox="0 0 5 8"><path d="M1 1l3 3-3 3" stroke="#fff" stroke-width="1.3" fill="none"/></svg></span></div>
  <div class="book-rows">
    <div class="book-row"><span class="c1">With Mock Services</span><span class="c2">$5.99</span><span class="c3">Buy from Us</span><span class="c4">Buy from Riverstore</span></div>
    <div class="book-row"><span class="c1">With KnotJS Services</span><span class="c2">$5.99</span><span class="c3">Buy from Us</span><span class="c4">Buy from Riverstore</span></div>
    <div class="book-row"><span class="c1">With FrostForge Services</span><span class="c2">$5.99</span><span class="c3">Buy from Us</span><span class="c4">Buy from Riverstore</span></div>
    <div class="book-row"><span class="c1">Buy Them All</span><span class="c2">$9.99</span><span class="c3">Buy from Us</span></div>
  </div>
</section>

<section class="book rust" style="top:766px">
  <div class="book-head"><span>AnvilJS 2 &amp; Strapkit</span><span class="view">View App <svg width="5" height="8" viewBox="0 0 5 8"><path d="M1 1l3 3-3 3" stroke="#fff" stroke-width="1.3" fill="none"/></svg></span></div>
  <div class="book-rows">
    <div class="book-row"><span class="c1">With Mock Services</span><span class="c2">$5.99</span><span class="c3">Buy from Us</span><span class="c4">Buy from Riverstore</span></div>
    <div class="book-row"><span class="c1">With KnotJS Services</span><span class="c2">$5.99</span><span class="c3">Buy from Us</span><span class="c4">Buy from Riverstore</span></div>
    <div class="book-row"><span class="c1">With FrostForge Services</span><span class="c2">$5.99</span><span class="c3">Buy from Us</span><span class="c4">Buy from Riverstore</span></div>
    <div class="book-row"><span class="c1">Buy Them All</span><span class="c2">$9.99</span><span class="c3">Buy from Us</span></div>
  </div>
</section>

<section class="book green" style="top:903px">
  <div class="book-head"><span>ReflexJS</span><span class="view">View App <svg width="5" height="8" viewBox="0 0 5 8"><path d="M1 1l3 3-3 3" stroke="#fff" stroke-width="1.3" fill="none"/></svg></span></div>
  <div class="book-rows">
    <div class="book-row"><span class="c1">With Mock Services</span><span class="c2">$5.99</span><span class="c3">Buy from Us</span><span class="c4">Buy from Riverstore</span></div>
    <div class="book-row"><span class="c1">With KnotJS Services</span><span class="c2">$5.99</span><span class="c3">Buy from Us</span><span class="c4">Buy from Riverstore</span></div>
    <div class="book-row"><span class="c1">With FrostForge Services</span><span class="c2">$5.99</span><span class="c3">Buy from Us</span><span class="c4">Buy from Riverstore</span></div>
    <div class="book-row"><span class="c1">Buy Them All</span><span class="c2">$9.99</span><span class="c3">Buy from Us</span></div>
  </div>
</section>

<footer class="site-footer">
  <div class="partner" style="left:107px;color:#c8262c"><i style="background:#c8262c"></i>NetPivot Consulting</div>
  <div class="partner" style="left:320px;color:#3a3a8c"><i style="background:#3a3a8c"></i>Plumvane</div>
  <div class="partner" style="left:495px;color:#2f5fb3"><i style="background:#2f5fb3"></i>BeyondTheGrid</div>
  <div class="footer-rule"></div>
  <nav class="footer-nav">
    <a style="left:109px">Home</a>
    <a style="left:155px">About Us</a>
    <a style="left:217px">Technology</a>
    <a style="left:290px">Shop Book</a>
    <a style="left:359px">Resources</a>
    <a style="left:426px">Contact</a>
  </nav>
  <div class="copyright">© 2016 Company Name &nbsp;All right reserved &nbsp;Term of Use</div>
  <span class="social" style="left:505px" aria-label="Social link"></span>
  <span class="social" style="left:532px" aria-label="Social link"></span>
  <span class="social" style="left:559px" aria-label="Social link"></span>
  <span class="social" style="left:586px" aria-label="Social link"></span>
  <span class="social" style="left:613px" aria-label="Social link"></span>
</footer>

</body>
</html>
```